Automotive eCommerce Business looking for a business card design

Looking for a clean and simple business card design. Our company name is "Brindle Auto" and we are a company specializing in the ecommerce sales of automotive parts, specifically for pick up trucks and large SUVs. Our company colours are red, black, and white.

Feel free to use the logo provided or create a new logo that you seem fit. Looking forward to your creative ideas!

Industry/Entity Type

Automotive

Contact Information for Business Card

We were thinking of a possibly two-sided design featuring just the logo and company name on one side, and personal information on the other side. Single sided designs will be considered as well.

Font styles to use
Serif
Sans Serif
Decorative

Colors
ec1f27
ffffff
000000

Requirements
Must have
• Space for employee's name, title, phone number and email address, along with the company address and website somewhere.

```html
<!DOCTYPE html>
<html lang="en">
<head>
<meta charset="utf-8">
<title>Brindle Auto – Business Card</title>
<link href="https://fonts.googleapis.com/css2?family=Arimo:wght@400;700&family=Noto+Serif:wght@700&display=swap" rel="stylesheet">
<style>
  :root {
    --stage: #2b2b2b;
    --brand-red: #9c1b22;
    --brand-red-deep: #7e141a;
    --ink: #111111;
    --paper: #ffffff;
  }
  html, body {
    margin: 0;
    width: 1200px;
    height: 997px;
    overflow: hidden;
    background: var(--stage);
  }
  .stage {
    position: relative;
    width: 1200px;
    height: 997px;
  }
  .card {
    position: absolute;
    top: 347px;
    width: 530px;
    height: 303px;
    overflow: hidden;
    box-shadow: 0 10px 30px rgba(0,0,0,.55);
  }
  /* Back side: brand only */
  .card--back {
    left: 50px;
    background: linear-gradient(160deg, #a81e26 0%, var(--brand-red-deep) 100%);
    display: flex;
    align-items: center;
    justify-content: center;
  }
  .brand-lockup {
    display: flex;
    align-items: center;
    gap: 14px;
  }
  .brand-lockup__mark {
    width: 40px;
    height: 40px;
    background: var(--paper);
  }
  .brand-lockup__name {
    font-family: "Noto Serif", Georgia, serif;
    font-weight: 700;
    font-size: 46px;
    color: var(--paper);
    letter-spacing: .5px;
  }
  /* Front side: personal details */
  .card--front {
    left: 620px;
    background: var(--paper);
  }
  .card__art {
    position: absolute;
    inset: 0;
  }
  .front-brand {
    position: absolute;
    top: 36px;
    left: 0;
    right: 0;
    display: flex;
    justify-content: center;
    align-items: center;
    gap: 12px;
  }
  .front-brand__mark {
    width: 46px;
    height: 46px;
    background: var(--brand-red);
  }
  .front-brand__name {
    font-family: "Noto Serif", Georgia, serif;
    font-weight: 700;
    font-size: 30px;
    color: var(--brand-red);
  }
  .person {
    position: absolute;
    top: 104px;
    left: 0;
    right: 0;
    text-align: center;
    font-family: "Arimo", Arial, sans-serif;
    font-weight: 700;
    line-height: 1.1;
  }
  .person__name {
    font-size: 15px;
    color: var(--brand-red);
    letter-spacing: .5px;
  }
  .person__title {
    font-size: 12px;
    color: var(--ink);
    letter-spacing: .5px;
  }
  .contact {
    position: absolute;
    top: 178px;
    left: 0;
    right: 0;
    text-align: center;
    font-family: "Arimo", Arial, sans-serif;
    color: var(--paper);
  }
  .contact__icons {
    display: flex;
    justify-content: center;
    gap: 10px;
    margin-bottom: 6px;
  }
  .contact__icons svg { width: 16px; height: 16px; }
  .contact__line {
    font-size: 15px;
    line-height: 22px;
    letter-spacing: .8px;
  }
</style>
</head>
<body>
<main class="stage">

  <section class="card card--back" aria-label="Business card, back">
    <div class="brand-lockup">
      <span class="brand-lockup__mark"></span>
      <span class="brand-lockup__name">Brindle Auto</span>
    </div>
  </section>

  <section class="card card--front" aria-label="Business card, front">
    <svg class="card__art" viewBox="0 0 530 303" aria-hidden="true">
      <path d="M0,285 C120,205 300,158 530,148 L530,303 L0,303 Z" fill="var(--brand-red)"/>
      <path d="M60,258 C170,185 340,140 520,130 C345,134 180,180 60,258 Z" fill="var(--ink)"/>
    </svg>

    <div class="front-brand">
      <span class="front-brand__mark"></span>
      <span class="front-brand__name">Brindle Auto</span>
    </div>

    <div class="person">
      <div class="person__name">DANIEL R. HOLLIS</div>
      <div class="person__title">PRESIDENT</div>
    </div>

    <div class="contact">
      <div class="contact__icons">
        <svg viewBox="0 0 16 16" aria-label="Phone"><circle cx="8" cy="8" r="8" fill="#fff"/><path d="M5 4.5h2l.6 2-1 .8a5 5 0 0 0 2.1 2.1l.8-1 2 .6v2c0 .5-.4.9-1 .9A6.5 6.5 0 0 1 4.1 5.4c0-.5.4-.9.9-.9z" fill="var(--brand-red)"/></svg>
        <svg viewBox="0 0 16 16" aria-label="Email"><circle cx="8" cy="8" r="8" fill="#fff"/><rect x="4" y="5.2" width="8" height="5.6" fill="var(--brand-red)"/><path d="M4 5.4l4 3 4-3" fill="none" stroke="#fff" stroke-width=".9"/></svg>
        <svg viewBox="0 0 16 16" aria-label="Address"><circle cx="8" cy="8" r="8" fill="#fff"/><path d="M8 3.6a3 3 0 0 1 3 3c0 2.2-3 5.8-3 5.8S5 8.8 5 6.6a3 3 0 0 1 3-3z" fill="var(--brand-red)"/><circle cx="8" cy="6.6" r="1.1" fill="#fff"/></svg>
      </div>
      <div class="contact__line">04821-336190-0</div>
      <div class="contact__line">name@brindle-parts.de</div>
      <div class="contact__line">Lindenweg 12,40210 Kessel</div>
    </div>
  </section>

</main>
</body>
</html>
```